Brochure for dynamic theatrical production company

New brochure for Heron Stageworks, featuring our current theatrical projects. We are a theatrical producing and consulting company, and we need the brochure to communicate the breadth of our projects. Our work is produced and performed throughtout the United States and also tours to Europe, Asia, the Middle East and South America. We also work with companies and artists from around the globe and bring them to the United States to tour and develop new work. Projects range from experimental multi-disciplinary works to Broadway musicals.

The brochure is meant to introduce other performing arts professionals to our work. These potential clients might engage one of our artists or projects for a performance, or they may engage us as consultants on additional projects.

The final design should be a standard size document that is fairly simple and inexpensive to reproduce. This is a piece that is used within the entertainment industry to develop interest in our work from other theaters, presenters, festivals, donors and artists.

I have included the pdf of last year's design, as well as a word document with the text to be used for this year. The world document also contains a link to a dropbox folder with photos and other supplementary materials as well.

You can also refer to our website for insights into our work and our aesthetic. www.heronstageworks-example.com

Target Market(s)

Industry professionals, funders/investors, prospective clients.

Industry/Entity Type

Entertainment Industry

Font styles to use
Sans Serif

Colors

Designer to choose colors to be used in the design.

Requirements
Must have
• Please use text provided in "Heron Brochure 2018" document. A variety of photos and other graphics are available for download via a link embedded in the document.
• Please make sure the finished piece can be printed on standard paper sizes in the US: For example: ledger size is 279 x 432 mm (11.0 x 17.0 in), letter size is 216 x 279 mm (8.5 x 11.0 in), Legal size is 216 x 356 mm (8.5 x 14.0 in)
Nice to have
• Our previous brochure and current website use pictures in the shape of circles (see sample attached). I would like that to be consistent with the new brochure. Website, for your reference, is www.heronstageworks-example.com
Should not have
• non-standard paper sizes

```html
<!DOCTYPE html>
<html lang="en">
<head>
<meta charset="utf-8">
<title>Heron Stageworks – Contact</title>
<link rel="stylesheet" href="https://fonts.googleapis.com/css2?family=Arimo:wght@400;700&display=swap">
<style>
  :root {
    --teal: #1ea3b1;
    --teal-soft: #3bb3bf;
    --ink: #111111;
    --grey: #555555;
    --paper: #ffffff;
    --stage-dark: #0b0b10;
    --stage-violet: #3b3370;
  }
  html, body {
    margin: 0;
    padding: 0;
    width: 927px;
    height: 1200px;
    overflow: hidden;
    background: var(--paper);
  }
  .back-cover {
    position: relative;
    width: 927px;
    height: 1200px;
    overflow: hidden;
    background: var(--paper);
    font-family: "Arimo", Arial, sans-serif;
  }
  .feature-circle {
    position: absolute;
    left: 0;
    top: 0;
    width: 927px;
    height: 1200px;
  }
  .contact-block {
    position: absolute;
    left: 254px;
    top: 408px;
    font-size: 13px;
    line-height: 16.4px;
    color: var(--grey);
  }
  .contact-heading {
    margin: 0 0 16px;
    font-weight: 400;
    font-size: 13px;
    color: var(--teal);
    letter-spacing: 0.1px;
  }
  .contact-person {
    margin: 0 0 16px;
  }
  .contact-name {
    display: block;
    font-weight: 700;
    color: var(--ink);
  }
  .contact-line { display: block; }
  .contact-visit { margin: 0; }
  .contact-visit a {
    margin-left: 6px;
    font-weight: 700;
    color: var(--ink);
    text-decoration: none;
  }
  .brand-mark {
    position: absolute;
    left: 0;
    width: 927px;
    top: 1062px;
    display: flex;
    justify-content: center;
    align-items: center;
    gap: 10px;
  }
  .brand-dot {
    width: 22px;
    height: 22px;
    border-radius: 50%;
    background: var(--teal);
  }
  .brand-name {
    font-family: "Arimo", Arial, sans-serif;
    font-size: 30px;
    font-weight: 400;
    color: var(--ink);
    letter-spacing: -0.3px;
  }
</style>
</head>
<body>
<main class="back-cover">
  <svg class="feature-circle" viewBox="0 0 927 1200" aria-hidden="false">
    <defs>
      <linearGradient id="ringFade" x1="0" y1="0" x2="0" y2="1">
        <stop offset="0" stop-color="#2fb0bb"/>
        <stop offset="0.45" stop-color="#7fcdd4"/>
        <stop offset="0.78" stop-color="#e4f4f6" stop-opacity="0.9"/>
        <stop offset="0.92" stop-color="#ffffff" stop-opacity="0"/>
      </linearGradient>
      <radialGradient id="stageGlow" cx="0.3" cy="0.85" r="0.6">
        <stop offset="0" stop-color="#5b4a9a"/>
        <stop offset="0.4" stop-color="#1a1730"/>
        <stop offset="1" stop-color="#0b0b10"/>
      </radialGradient>
    </defs>
    <circle class="ring" cx="1184" cy="640" r="410" fill="url(#ringFade)"/>
    <circle class="photo-border" cx="1184" cy="622" r="292" fill="#ffffff"/>
    <circle class="photo" cx="1184" cy="622" r="285" fill="url(#stageGlow)"
            role="img" aria-label="Circular production photo of a performer on a darkly lit stage"/>
  </svg>

  <section class="contact-block">
    <h2 class="contact-heading">FOR MORE INFORMATION CONTACT:</h2>

    <p class="contact-person">
      <span class="contact-name">Dana Whitlock</span>
      <span class="contact-line">Executive/Creative Producer</span>
      <span class="contact-line">dana@heronstageworks-example.com</span>
      <span class="contact-line">(555) 014-2230</span>
    </p>

    <p class="contact-person">
      <span class="contact-name">Lena Marsh</span>
      <span class="contact-line">Associate Producer</span>
      <span class="contact-line">lena@heronstageworks-example.com</span>
      <span class="contact-line">(555) 018-4471</span>
    </p>

    <p class="contact-person">
      <span class="contact-name">Owen Pratt</span>
      <span class="contact-line">Production Coordinator</span>
      <span class="contact-line">owen@heronstageworks-example.com</span>
    </p>

    <p class="contact-visit">Or VISIT: <a href="#">www.heronstageworks-example.com/resources</a></p>
  </section>

  <div class="brand-mark">
    <span class="brand-dot"></span>
    <span class="brand-name">Heron Stageworks</span>
  </div>
</main>
</body>
</html>
```